New Food Sleeve Design for British Traditional Food Manufacture - est 1976

We are a food manufacturer of a British traditional Steamed 'Rag Pudding' this is a Lancashire traditional dish. It consists of finest cuts of beef, hand wrapped in a suet pastry. Then traditionally wrapped in a rag (muslin cloth) today we use a modern plastic version to wrap the pudding then it is steamed, to create a beautiful tasting beef pudding (which is essentially a pie or parcel).
We are looking for a design on a newly developed packaging, which is basically a sleeve with two stays at either end so the product can not slip out of the packaging.
We would like to see designs that have :
1. a picture of the cooked product on the top of the sleeve - so customers can see what they will get once cooked.
2. The bottom of the package is for the ingredients, barcode best before date - We have this in hand so please do not design anything on the bottom of the package.
3.The front with the push tap and the opposite rear can be for cooking instructions or further info - we have no preference ein this area.
4. Wording/art required:
- Picture of the cooked product (I have a photo attached that can be used for now - but we intend to upgrade this photo at a later)
- Picture of the little man - however this man can be upgraded as it is 40 years old
- Wording 'Est 1976'
- if possible a British flag & wording 'Made in Britain'
=Wording 'Pemberton's Beef Pudding'
- Cooking instructions - maybe use of symbols - Oven bake, Steam, Boil in the bag, Microwave. But these could potentially go on the smaller front or rear location
- We would like a black, dark grey etc colour as the background - we feel this is currently a luxurious/quality look' at the moment.
- But we are open to other colours if you want to experiment

Info attached to help you...
- We have attached the pdf of the dimensions of the packaging
- Photo of beef pudding - happy for you to remove the chips and peas if that helps
- Link to current website - www.steamparcelworks.co.uk
- The little man (as mentioned happy for an upgrade) we don't need the writing along with the little man
- a few photos of how the packaging works and looks (photos of stages 1 to 6)
- a few design attached of what we like, but we are not stuck to this happy to see different ideas

Update 19th January 2023
We have lots of great designs, each with parts we like. I'd like to provide some overall feedback of the items we like from the designs submitted to date:
-The little man logo. We really like the British flag represented on the apron. We think if Pembertons dale larder can be removed from this logo and keep the words 'quality with convenience', 'made in Britain ' & EST 1976. I think that would be great.
-we think the pudding on its own rather than with chips and peas looks better and gives a clear indication of what the customer is buying.
-we don't need sell by/best before/batch number on the front as this will be on the rear and on the internal packaging
-do like/need the colour chart for salt/sugar/fat etc - but currently have no preference to if it's on the top or front.
-do like the symbols for cooking, but not sure we like one we have seen yet.
-lile the idea of golden/golden orange colour text in places
-really like the slight band of colour as this could be simple changed to an alternative colour for other products with have.
Hope this helps you all

Target Market(s)

Basically anyone who has an evening meal who likes to eat meat

Industry/Entity Type

Food maufacturing

Colors

Designer to choose colors to be used in the design.

Requirements
Must have
• A picture of the product when cooked
Nice to have
• Little man, established 1976, made in Britain

```html
<!DOCTYPE html>
<html lang="en">
<head>
<meta charset="utf-8">
<title>Pemberton's Beef Pudding – Lancashire Original</title>
<link rel="stylesheet" href="https://fonts.googleapis.com/css2?family=Arimo:ital,wght@0,400;0,700;1,400&family=Jost:wght@300&display=swap">
<style>
  :root {
    --plum-top: #5a1d4a;
    --plum-mid: #3a0f33;
    --plum-deep: #1a0514;
    --sleeve: #2d2c2a;
    --sleeve-edge: #1f1e1c;
    --gold: #e3a23a;
    --cream: #f1ede6;
    --meat-light: #e8a94a;
    --meat-dark: #7a2d12;
    --flag-blue: #1f3f8c;
    --flag-red: #c8102e;
    --white: #ffffff;
  }
  * { box-sizing: border-box; margin: 0; padding: 0; }
  html, body { width: 900px; height: 1200px; overflow: hidden; }
  body { font-family: "Arimo", Arial, sans-serif; }

  .poster {
    position: relative;
    width: 900px;
    height: 1200px;
    background: linear-gradient(180deg, var(--plum-top) 0%, var(--plum-mid) 45%, var(--plum-deep) 100%);
    overflow: hidden;
  }

  .sleeve {
    position: absolute;
    left: 100px;
    top: 590px;
    width: 800px;
    height: 290px;
    background: var(--sleeve);
    box-shadow: 0 10px 40px rgba(0,0,0,.55);
    display: flex;
  }

  .flag {
    position: absolute;
    left: 100px;
    top: 562px;
    width: 146px;
    height: 82px;
    z-index: 2;
  }

  .brand-block {
    width: 450px;
    display: flex;
    flex-direction: column;
    align-items: center;
    padding-top: 78px;
    text-align: center;
  }
  .brand-mark {
    display: flex;
    align-items: center;
    gap: 14px;
  }
  .brand-dot {
    width: 22px; height: 22px;
    border-radius: 50%;
    background: var(--gold);
  }
  .brand-name {
    font-weight: 700;
    font-size: 38px;
    line-height: 1.05;
    color: var(--cream);
    text-transform: uppercase;
    letter-spacing: .5px;
  }
  .product-type {
    margin-top: 14px;
    font-weight: 700;
    font-size: 15px;
    color: var(--gold);
    letter-spacing: .6px;
  }
  .tagline {
    margin-top: 22px;
    font-style: italic;
    font-size: 18px;
    color: var(--cream);
    letter-spacing: .6px;
  }
  .origin {
    margin-top: 20px;
    font-size: 12px;
    line-height: 1.35;
    color: var(--gold);
    letter-spacing: 1.6px;
  }

  .serving-side {
    flex: 1;
    display: flex;
    flex-direction: column;
  }
  .serving-photo {
    height: 232px;
    margin-top: 10px;
    background: radial-gradient(ellipse at 55% 55%, var(--meat-dark) 0%, #a8461a 35%, var(--meat-light) 70%, #f3c46c 100%);
  }
  .cooking-methods {
    flex: 1;
    display: flex;
    justify-content: space-around;
    align-items: center;
    padding: 0 6px;
  }
  .method {
    display: flex;
    flex-direction: column;
    align-items: center;
    color: var(--gold);
    font-size: 7px;
    font-weight: 700;
    gap: 2px;
  }
  .method svg { width: 22px; height: 16px; }

  .headline {
    position: absolute;
    left: 110px;
    top: 990px;
    font-family: "Jost", "Helvetica Neue", sans-serif;
    font-weight: 300;
    font-size: 78px;
    line-height: 1.02;
    color: var(--gold);
    letter-spacing: 1px;
  }
</style>
</head>
<body>
  <main class="poster">
    <svg class="flag" viewBox="0 0 60 34" role="img" aria-label="British flag" preserveAspectRatio="none">
      <rect width="60" height="34" fill="var(--flag-blue)"/>
      <path d="M0 0 L60 34 M60 0 L0 34" stroke="var(--white)" stroke-width="7"/>
      <path d="M0 0 L60 34 M60 0 L0 34" stroke="var(--flag-red)" stroke-width="2.4"/>
      <path d="M30 0 V34 M0 17 H60" stroke="var(--white)" stroke-width="10"/>
      <path d="M30 0 V34 M0 17 H60" stroke="var(--flag-red)" stroke-width="6"/>
    </svg>

    <section class="sleeve">
      <div class="brand-block">
        <div class="brand-mark">
          <span class="brand-dot"></span>
          <h1 class="brand-name">Pemberton's<br>Beef Pudding</h1>
        </div>
        <p class="product-type">TRADITIONAL LANCASHIRE RAG PUDDING</p>
        <p class="tagline">Quality With Convenience</p>
        <p class="origin">MADE IN BRITAIN<br>EST 1976</p>
      </div>

      <div class="serving-side">
        <div class="serving-photo" role="img" aria-label="Close-up photo of a cooked beef rag pudding cut open, showing suet pastry and beef filling"></div>
        <div class="cooking-methods">
          <div class="method">
            <span>10-15 min</span>
            <svg viewBox="0 0 22 16"><rect x="2" y="2" width="18" height="12" rx="1" fill="none" stroke="currentColor" stroke-width="1.6"/><rect x="5" y="6" width="12" height="6" fill="currentColor"/></svg>
            <span>Oven Baked</span>
          </div>
          <div class="method">
            <span>10-25 min</span>
            <svg viewBox="0 0 22 16"><rect x="2" y="2" width="18" height="12" rx="1" fill="none" stroke="currentColor" stroke-width="1.6"/><rect x="4" y="4" width="11" height="8" fill="currentColor"/><circle cx="17.5" cy="6" r="1" fill="currentColor"/></svg>
            <span>Microwave Baked</span>
          </div>
          <div class="method">
            <span>10 min</span>
            <svg viewBox="0 0 22 16"><path d="M7 13 Q11 9 7 5 M11 13 Q15 9 11 5 M15 13 Q19 9 15 5" fill="none" stroke="currentColor" stroke-width="1.6"/></svg>
            <span>Steam Boiled</span>
          </div>
          <div class="method">
            <span>15 min</span>
            <svg viewBox="0 0 22 16"><path d="M9 2 H13 L12 5 Q18 8 17 15 H5 Q4 8 10 5 Z" fill="currentColor"/></svg>
            <span>Bag Boiled</span>
          </div>
        </div>
      </div>
    </section>

    <h2 class="headline">LANCASHIRE<br>ORIGINAL</h2>
  </main>
</body>
</html>
```